Construction company business card

One side to be the logo with the company name, The other side I would like: (Tomas verbick) Project manager 41 barrow crescent kelvale 52917306224783(03) 9703 2428Info@gudeljgroup.comAnd then maybe a couple dot points saying what we do:Construction (commercial & industrial) Civil construction

Anything else please contact me!
Maybe curved st one edge of the card

Target Market(s)

Older clientele

Industry/Entity Type

Construction Company

Contact Information for Business Card

Read above

Colors
3277b5
1b1b1b
9d9d9d

Requirements
Must have
• Use my logo on one side
Nice to have
• Read above
Should not have
• Read above

```html
<!DOCTYPE html>
<html lang="en">
<head>
<meta charset="utf-8">
<title>Steadform Property Group – Business Card</title>
<link href="https://fonts.googleapis.com/css2?family=Open+Sans:wght@400;600;700&display=swap" rel="stylesheet">
<style>
  :root {
    --brand-blue: #3277b5;
    --ink: #1b1b1b;
    --grey: #9d9d9d;
    --paper: #fbfbfb;
    --backdrop: #e9e7e4;
    --mark-light: #dfe9f3;
    --rule: #e2e2e2;
  }
  * { box-sizing: border-box; margin: 0; padding: 0; }
  html, body {
    width: 1200px; height: 844px; overflow: hidden;
    background: var(--backdrop);
    font-family: "Open Sans", Arial, sans-serif;
  }
  .stage {
    position: relative; width: 1200px; height: 844px;
    display: flex; align-items: center; justify-content: center; gap: 60px;
  }
  .card {
    position: relative; width: 500px; height: 306px;
    border-radius: 4px; box-shadow: 0 6px 18px rgba(0,0,0,.18);
    overflow: hidden;
  }
  /* Front: contact details */
  .card--front { background: var(--paper); color: var(--ink); }
  .brand {
    position: absolute; top: 34px; right: 34px;
    display: flex; align-items: center; gap: 12px;
  }
  .brand__dot {
    width: 46px; height: 46px; border-radius: 50%;
    background: var(--brand-blue); flex: none;
  }
  .brand__name {
    color: var(--brand-blue); font-weight: 700;
    font-size: 17px; line-height: 1.1; letter-spacing: .5px;
    text-transform: uppercase; width: 130px;
  }
  .divider {
    position: absolute; top: 118px; left: 200px; right: 34px;
    height: 1px; background: var(--rule);
  }
  .contact {
    position: absolute; left: 34px; bottom: 30px; right: 34px;
    font-size: 13px; line-height: 1.45;
  }
  .contact__name {
    color: var(--brand-blue); font-weight: 700; font-size: 19px;
    text-transform: uppercase; letter-spacing: .3px; line-height: 1.1;
  }
  .contact__role { color: #444; font-size: 13.5px; }
  .contact__lines { margin-top: 6px; }
  .label { color: var(--brand-blue); font-weight: 600; }
  .sep { color: var(--grey); padding: 0 3px; }
  .services {
    margin-top: 8px; list-style: none; display: flex; gap: 14px; flex-wrap: nowrap;
    white-space: nowrap;
  }
  .services li { display: flex; align-items: center; gap: 6px; }
  .services li::before {
    content: ""; width: 9px; height: 9px; border-radius: 50%;
    background: var(--brand-blue); flex: none;
  }
  /* Back: brand side */
  .card--back {
    background: var(--brand-blue);
    display: flex; align-items: center; justify-content: center;
  }
  .back-brand { display: flex; align-items: center; gap: 14px; }
  .back-brand__dot {
    width: 56px; height: 56px; border-radius: 50%; background: var(--mark-light); flex: none;
  }
  .back-brand__name {
    color: var(--mark-light); font-weight: 700; font-size: 20px;
    text-transform: uppercase; letter-spacing: .6px; line-height: 1.15; width: 150px;
  }
</style>
</head>
<body>
<main class="stage">
  <section class="card card--front" aria-label="Business card front">
    <div class="brand">
      <span class="brand__dot"></span>
      <span class="brand__name">Steadform Property Group</span>
    </div>
    <div class="divider"></div>
    <div class="contact">
      <p class="contact__name">Tomas Verbick</p>
      <p class="contact__role">Project manager</p>
      <div class="contact__lines">
        <p>41 barrow crescent kelvale 5291</p>
        <p><span class="label">P:</span> 7306224783<span class="sep">|</span><span class="label">M:</span> (03) 9418 6573<span class="sep">|</span><span class="label">E:</span> Info@verbickgroup.com</p>
      </div>
      <ul class="services">
        <li>Construction (commercial &amp; industrial)</li>
        <li>Civil construction</li>
      </ul>
    </div>
  </section>

  <section class="card card--back" aria-label="Business card back">
    <div class="back-brand">
      <span class="back-brand__dot"></span>
      <span class="back-brand__name">Steadform Property Group</span>
    </div>
  </section>
</main>
</body>
</html>
```